Business Card Design Project

Looking for a logo and business card for a Real State Business i will be opening. The name is not choosen yet , but will probably be RWT IMOVEIS.
I was thinking black and silver colors, but am open to nice ideas.
I did add a business card that i liked a lot, am looking for something like that, with logo in black or silver in a black card. The logo i was thinking in the letters RWT as i uploaded or something or little and cute buildings or a house...just ideas, can be any nice logo.
Updates

You guys can add other colors if you want, I like colors very "BRIGHT" and "open", like red, pink, strong colors. almost glow in the dark colors. lol

Designers,

I've increased more 88 dollars in the budget for 1st place cause I will want envelope designs... small and big sizes.

So 1st place is now U$248,00. 

No need to send the envelope designs right now... only the business cards designs.

Thank you.

Industry/Entity Type

Business

Requirements
Must have
• Marcela Tavares Rocha

www.RWTimoveis-exemplo.com.br

+554187316042

marcela@rwtimoveis-exemplo.com.br

```html
<!DOCTYPE html>
<html lang="pt-BR">
<head>
<meta charset="utf-8">
<title>RWT Imoveis – Business Card</title>
<link rel="stylesheet" href="https://fonts.googleapis.com/css2?family=Cinzel:wght@600&family=Arimo:wght@400&display=swap">
<style>
  :root {
    --backdrop: #1c1c1c;
    --card: #0b0707;
    --card-edge: #2a2424;
    --white: #ffffff;
    --silver: #a4a4a4;
    --muted: #8a8a8a;
  }
  * { margin: 0; padding: 0; box-sizing: border-box; }
  html, body {
    width: 1200px;
    height: 928px;
    overflow: hidden;
    background: var(--backdrop);
  }
  .canvas {
    position: relative;
    width: 1200px;
    height: 928px;
  }
  .card {
    position: absolute;
    width: 660px;
    height: 420px;
    background: var(--card);
    border: 1px solid var(--card-edge);
  }
  .card--back { left: 90px; top: 40px; }
  .card--front { left: 450px; top: 468px; }

  .brand {
    position: absolute;
    display: flex;
    align-items: center;
    font-family: "Cinzel", serif;
    font-weight: 600;
    white-space: nowrap;
    transform: translate(-50%, -50%);
  }
  .brand__name {
    display: flex;
    flex-direction: column;
    align-items: center;
    line-height: 1.05;
  }
  .brand__dot {
    border-radius: 50%;
    flex: none;
  }

  .card--back .brand {
    left: 50%;
    top: 50%;
    gap: 26px;
    font-size: 76px;
    color: var(--silver);
  }
  .card--back .brand__dot {
    width: 56px; height: 56px;
    background: var(--silver);
  }

  .card--front .brand {
    left: 195px;
    top: 200px;
    gap: 16px;
    font-size: 40px;
    color: var(--white);
  }
  .card--front .brand__dot {
    width: 30px; height: 30px;
    background: var(--white);
  }

  .contact {
    position: absolute;
    left: 385px;
    top: 240px;
    font-family: "Arimo", Arial, sans-serif;
    font-style: normal;
    font-size: 13.5px;
    line-height: 18px;
    color: var(--white);
  }
  .contact__name {
    color: var(--muted);
    font-size: 14.5px;
  }
</style>
</head>
<body>
  <main class="canvas">
    <section class="card card--back" aria-label="Card back">
      <div class="brand">
        <span class="brand__dot"></span>
        <span class="brand__name"><span>RWT</span><span>IMOVEIS</span></span>
      </div>
    </section>

    <section class="card card--front" aria-label="Card front">
      <div class="brand">
        <span class="brand__dot"></span>
        <span class="brand__name"><span>RWT</span><span>IMOVEIS</span></span>
      </div>
      <address class="contact">
        <p class="contact__name">Marcela Tavares Rocha</p>
        <p class="contact__email">marcela@rwtimoveis-exemplo.com.br</p>
        <p class="contact__web">www.RWTimoveis-exemplo.com.br</p>
        <p class="contact__phone">554187316042</p>
      </address>
    </section>
  </main>
</body>
</html>
```